Harborline Auto LLC

Car Dealer Customer Service
Address: 2874 Cresthaven Road, Larkmoor Falls, WA 98999
web: www.harborlineautoxq.net
email: harborlineautoxq@mailnest.example
Phone: (555) 555-0148
Phone: (555) 555-0173

```html
<!DOCTYPE html>
<html lang="en">
<head>
<meta charset="utf-8">
<title>Harborline Auto – Business Card</title>
<link href="https://fonts.googleapis.com/css2?family=Montserrat:wght@400;500;800&display=swap" rel="stylesheet">
<style>
  :root {
    --bg: #1b1b1d;
    --paper: #f7f7f5;
    --blue: #1f86c3;
    --blue-deep: #176ea8;
    --blue-light: #2a98d2;
    --gold: #ebb445;
    --ink: #4a4a4a;
  }
  * { box-sizing: border-box; margin: 0; padding: 0; }
  html, body { width: 1200px; height: 963px; overflow: hidden; }
  body {
    background: var(--bg);
    font-family: "Montserrat", sans-serif;
    display: flex; flex-direction: column; align-items: center; justify-content: center;
    gap: 60px;
  }
  .card {
    position: relative; width: 700px; height: 400px; overflow: hidden;
    border-radius: 4px; box-shadow: 0 14px 30px rgba(0,0,0,.5);
  }
  .card-front { background: var(--paper); }
  .card-front .waves { position: absolute; inset: 0; width: 100%; height: 100%; }
  .brand {
    position: absolute; left: 150px; top: 52px;
    display: flex; align-items: center; gap: 12px;
  }
  .brand-dot { width: 34px; height: 34px; border-radius: 50%; background: var(--gold); flex: none; }
  .brand-name {
    font-weight: 800; font-size: 26px; color: var(--blue-deep);
    letter-spacing: .5px; text-transform: uppercase; white-space: nowrap;
  }
  .address {
    position: absolute; left: 70px; top: 118px;
    font-size: 15px; line-height: 21px; color: var(--ink);
  }
  .contacts { position: absolute; left: 70px; top: 172px; list-style: none; }
  .contacts li {
    display: flex; align-items: center; gap: 8px;
    font-size: 15px; line-height: 22px; color: var(--ink); white-space: nowrap;
  }
  .contacts svg { width: 14px; height: 14px; flex: none; }
  .person { position: absolute; right: 50px; top: 150px; text-align: right; }
  .person-name {
    font-weight: 500; font-size: 20px; color: var(--gold);
    letter-spacing: 1.5px; text-transform: uppercase;
  }
  .person-role { font-size: 15px; color: var(--ink); margin-top: 4px; }
  .card-back {
    background: linear-gradient(135deg, var(--blue-light) 0%, var(--blue) 55%, var(--blue-deep) 100%);
    display: flex; align-items: center; justify-content: center;
  }
  .card-back .brand { position: static; gap: 18px; }
  .card-back .brand-dot { width: 56px; height: 56px; background: var(--paper); }
  .card-back .brand-name { color: #fff; font-size: 40px; }
</style>
</head>
<body>

<section class="card card-front">
  <svg class="waves" viewBox="0 0 700 400" preserveAspectRatio="none" aria-hidden="true">
    <path d="M150 400 C340 390 530 330 700 262 L700 400 Z" fill="var(--gold)"/>
    <path d="M0 305 C240 385 500 345 700 240 L700 256 C520 340 320 396 130 400 L110 400 C70 365 35 335 0 322 Z" fill="var(--blue)"/>
    <path d="M0 305 C240 385 500 345 700 240 L700 246 C500 355 240 392 0 312 Z" fill="var(--blue-deep)"/>
  </svg>

  <div class="brand">
    <span class="brand-dot"></span>
    <span class="brand-name">Harborline Auto</span>
  </div>

  <p class="address">2874 Cresthaven Road<br>Larkmoor Falls, WA 98999</p>

  <ul class="contacts">
    <li>
      <svg viewBox="0 0 14 14"><circle cx="7" cy="7" r="7" fill="var(--gold)"/><path d="M4.5 3.5l1.5 1.6-.8 1c.5 1 1.2 1.7 2.2 2.2l1-.8 1.6 1.5-1 1.2C6.6 10 4 7.4 3.3 4.5z" fill="#fff"/></svg>
      (555) 555-0148
    </li>
    <li>
      <svg viewBox="0 0 14 14"><circle cx="7" cy="7" r="7" fill="var(--gold)"/><path d="M4.5 3.5l1.5 1.6-.8 1c.5 1 1.2 1.7 2.2 2.2l1-.8 1.6 1.5-1 1.2C6.6 10 4 7.4 3.3 4.5z" fill="#fff"/></svg>
      (555) 555-0173
    </li>
    <li>
      <svg viewBox="0 0 14 14"><circle cx="7" cy="7" r="7" fill="var(--gold)"/><rect x="3.5" y="4.5" width="7" height="5" fill="#fff"/><path d="M3.5 4.5L7 7.3 10.5 4.5" fill="none" stroke="var(--gold)" stroke-width=".9"/></svg>
      harborlineautoxq@mailnest.example
    </li>
    <li>
      <svg viewBox="0 0 14 14"><circle cx="7" cy="7" r="7" fill="var(--gold)"/><circle cx="7" cy="7" r="3.6" fill="none" stroke="#fff" stroke-width="1"/><path d="M3.4 7h7.2M7 3.4c-1.6 2-1.6 5.2 0 7.2M7 3.4c1.6 2 1.6 5.2 0 7.2" fill="none" stroke="#fff" stroke-width=".8"/></svg>
      www.harborlineautoxq.net
    </li>
  </ul>

  <div class="person">
    <p class="person-name">Marcus Delaney</p>
    <p class="person-role">Manager</p>
  </div>
</section>

<section class="card card-back">
  <div class="brand">
    <span class="brand-dot"></span>
    <span class="brand-name">Harborline Auto</span>
  </div>
</section>

</body>
</html>
```